Vantiqo custom business card design

Need a authentic, innovative business card design for a new mobile app business. I am uploading a few screen images from our app for you to view. I would like app design theme to match business card design. I can also send logo images.

```html
<!DOCTYPE html>
<html lang="en">
<head>
<meta charset="utf-8">
<title>Vantiqo Business Card</title>
<link rel="stylesheet" href="https://fonts.googleapis.com/css2?family=Montserrat:wght@500;700;800&family=Open+Sans:wght@400;600&display=swap">
<style>
  :root {
    --stage: #e9e6e1;
    --card-white: #f7f7f7;
    --card-black: #161616;
    --purple: #6a2fa0;
    --purple-soft: #8a55c0;
    --ink: #222222;
    --ink-soft: #3a3a3a;
    --back-type: #2c2c2c;
  }
  * { box-sizing: border-box; margin: 0; padding: 0; }
  html, body { width: 1200px; height: 942px; overflow: hidden; }
  body {
    background: var(--stage);
    display: flex;
    align-items: center;
    justify-content: center;
    gap: 60px;
    font-family: "Open Sans", Arial, sans-serif;
  }
  .card {
    position: relative;
    width: 530px;
    height: 303px;
    overflow: hidden;
    box-shadow: 0 10px 24px rgba(0,0,0,0.18);
  }
  /* Front */
  .card-front { background: var(--card-white); }
  .front-band {
    position: absolute;
    left: 0; bottom: 0;
    width: 230px; height: 30px;
    background: var(--purple);
    clip-path: polygon(0 0, 100% 0, 88% 100%, 0 100%);
  }
  .brand {
    position: absolute;
    left: 48px; top: 118px;
    display: flex; align-items: center; gap: 12px;
  }
  .brand-dot {
    width: 30px; height: 30px; border-radius: 50%;
    background: var(--purple);
  }
  .brand-name {
    font-family: "Montserrat", Arial, sans-serif;
    font-weight: 800;
    font-size: 32px;
    color: var(--ink);
    letter-spacing: -0.5px;
  }
  .divider {
    position: absolute;
    left: 262px; top: 62px;
    width: 2px; height: 150px;
    background: var(--purple);
  }
  .contact {
    position: absolute;
    left: 284px; top: 66px;
  }
  .person-name {
    font-family: "Montserrat", Arial, sans-serif;
    font-weight: 700;
    font-size: 24px;
    color: var(--ink);
    line-height: 1.1;
  }
  .job-title {
    font-size: 14px;
    color: var(--purple-soft);
    margin-top: 2px;
    margin-bottom: 14px;
  }
  .contact-list { list-style: none; }
  .contact-list li {
    display: flex; align-items: center; gap: 10px;
    font-size: 14px; color: var(--ink-soft);
    line-height: 26px;
  }
  .contact-list svg { width: 13px; height: 13px; flex: none; }
  /* Back */
  .card-back { background: var(--card-black); }
  .back-mark {
    position: absolute; inset: 0;
    display: flex; align-items: center; justify-content: center; gap: 18px;
  }
  .back-dot {
    width: 56px; height: 56px; border-radius: 50%;
    background: var(--purple);
  }
  .back-name {
    font-family: "Montserrat", Arial, sans-serif;
    font-weight: 800;
    font-size: 48px;
    color: var(--back-type);
    letter-spacing: -0.5px;
  }
</style>
</head>
<body>
  <section class="card card-front" aria-label="Business card front">
    <div class="front-band"></div>
    <div class="brand">
      <span class="brand-dot"></span>
      <span class="brand-name">Vantiqo</span>
    </div>
    <div class="divider"></div>
    <div class="contact">
      <p class="person-name">Your Name</p>
      <p class="job-title">Job Title</p>
      <ul class="contact-list">
        <li>
          <svg viewBox="0 0 14 14" aria-hidden="true"><rect x="3" y="1" width="8" height="12" rx="1.5" fill="none" stroke="#6a2fa0" stroke-width="1.5"/></svg>
          000 000 0000
        </li>
        <li>
          <svg viewBox="0 0 14 14" aria-hidden="true"><rect x="1" y="3" width="12" height="8" fill="#6a2fa0"/><path d="M1 3 L7 8 L13 3" fill="none" stroke="#f7f7f7" stroke-width="1.2"/></svg>
          youremail@xyz.com
        </li>
        <li>
          <svg viewBox="0 0 14 14" aria-hidden="true"><circle cx="7" cy="7" r="6" fill="#8a55c0"/><path d="M1 7 H13 M7 1 C4 4 4 10 7 13 M7 1 C10 4 10 10 7 13" fill="none" stroke="#f7f7f7" stroke-width="0.9"/></svg>
          www.yourwebsite.com
        </li>
      </ul>
    </div>
  </section>

  <section class="card card-back" aria-label="Business card back">
    <div class="back-mark">
      <span class="back-dot"></span>
      <span class="back-name">Vantiqo</span>
    </div>
  </section>
</body>
</html>
```